Project Overview:
We are looking to create a website for a monthly subscription IPTV service in WordPress. The website should provide a seamless user experience for customers to sign up for the service and manage their account information. We need the following pages: Home Page, Product Page, Sign-Up Page, and Account Information Page.

Home Page:
The Home Page design should be simple and clean, with a dark theme and minimalistic design elements. We would like to include graphics of popular movie shows displayed on multiple devices. The page should highlight the key benefits and features of our service and provide a clear call-to-action for visitors to sign up.

Product Page:
The Product Page should provide detailed information about our subscription tiers and pricing plans. It should highlight the key features of each plan and provide a clear comparison between them. The page should also include a call-to-action button for visitors to sign up.

Sign-Up Page:
The Sign-Up Page is the conversion page where members will sign up for the service. It should collect the following information: Name, Phone Number, Email, Password, and Payment Information. The design should be simple, intuitive, and easy to use. It should highlight the benefits of our service and provide a clear call-to-action for visitors to sign up.

Account Information Page:
The Account Information Page should allow members to view and manage their account details. It should include the following information: Profile Image, Contact Details, Password Management, Payment Information Management, and Membership Expiration Date. The design should be user-friendly, intuitive, and easy to navigate.

Goals: The primary goal of the website is to provide an easy-to-use portal for customers to sign up for the service and manage their account information. The website should be user-friendly and visually appealing to attract potential customers.

Scope: The scope of the project includes designing a home page, a sign-up page, an account information page, and a payment information page. The website should be designed to be responsive and accessible on desktop and mobile devices.

Design Preferences: The design should be clean, modern, and visually appealing. The use of a color palette that is consistent with the brand identity is recommended. The website should be easy to navigate and provide a clear call-to-action for users to sign up for the service.

FYI: The subscription service I am designing a website for is related to an IPTV service. IPTV stands for Internet Protocol Television, which is a digital television broadcasting protocol that uses the internet to deliver TV programs and videos to viewers. The website will allow customers to sign up for the IPTV service and access their account information such as user name and password, membership tier, name, and payment details. Please let me know if you have any further questions, and I would be happy to provide more details. Thank you!

Dear Designers,

Thank you for your participation in our project. After reviewing the designs received so far, we have decided to update the brief to better reflect our needs and preferences. We apologize for any confusion this may cause, but we believe that these changes will result in better design submissions and a more successful project overall.

The updated brief is as follows:

We are looking to create a website for WordPress.

Also, here is the updated Brief.

Project Title: WordPress Website Design for Monthly Subscription IPTV Service

Project Overview:
We are looking to create a website for a monthly subscription IPTV service. The website should provide a seamless user experience for customers to sign up for the service and manage their account information. We need the following pages: Home Page, Product Page, Sign-Up Page, and Account Information Page.

Home Page:

Product Page:

Sign-Up Page:

Account Information Page:

Design Preferences:
We prefer a dark theme with minimalistic design elements and hits of our logo colors. The website should be easy to use and navigate, with clear calls-to-action and simple, intuitive forms. The design should be optimized for mobile devices and load quickly.

We hope that these updates provide you with a clearer understanding of our requirements and preferences. Please let us know if you have any questions or concerns. We look forward to seeing your revised designs.

Thank you again for your participation.
We will guarantee this project as soon as we see something we like that meets the updated requirements.

The website's target audience is individuals who are interested in subscribing to the monthly service.

4 page

• One item for sale and a client profile section.

```html
<!DOCTYPE html>
<html lang="en">
<head>
<meta charset="UTF-8">
<title>Virelo IPTV</title>
<link href="https://fonts.googleapis.com/css2?family=Bangers&family=Poppins:wght@400;500;600;700&display=swap" rel="stylesheet">
<style>
:root{
  --red:#e3141b;
  --red-deep:#b10e13;
  --black:#0a0a0a;
  --dark:#141414;
  --panel:#1c1c1c;
  --white:#ffffff;
  --muted:#cfcfcf;
}
*{margin:0;padding:0;box-sizing:border-box}
html,body{width:1200px;height:2720px;overflow:hidden;background:var(--black)}
body{font-family:'Poppins',sans-serif;color:var(--white);position:relative}
.display{font-family:'Bangers',sans-serif;letter-spacing:1px;font-weight:400}
.abs{position:absolute}
.brand{font-family:'Bangers',sans-serif;color:var(--red);font-size:44px;letter-spacing:2px}

/* header + hero */
.hero{position:absolute;left:0;top:0;width:1200px;height:720px;background:var(--black);overflow:hidden}
.hero-band{position:absolute;right:0;top:0}
.nav{position:absolute;top:24px;left:100px;right:80px;display:flex;align-items:center}
.nav-links{display:flex;gap:40px;margin-left:auto;margin-right:54px;font-size:17px;font-weight:500}
.btn-outline{border:2px solid var(--white);padding:6px 20px;font-size:13px;font-weight:600;text-transform:uppercase}
.hero-title{left:100px;top:226px;width:470px;font-size:50px;line-height:1.05}
.hero-text{left:100px;top:332px;width:430px;font-size:14px;line-height:1.6;color:var(--muted)}
.signup-form{display:flex;width:440px;height:40px;background:var(--white)}
.signup-form span{flex:1;color:#555;font-size:13px;padding:10px 14px}
.signup-form b{background:var(--red);color:var(--white);font-size:12px;font-weight:700;padding:11px 28px;text-transform:uppercase}
.hero-visual{left:540px;top:250px;width:620px;height:420px;background:linear-gradient(135deg,#6f8fb0 0%,#c9d6e3 45%,#2d2d33 100%)}

/* about */
.about{position:absolute;top:720px;left:0;width:1200px;height:460px;background:var(--dark)}
.about-title{left:100px;top:48px;width:400px;font-size:46px;line-height:1.05}
.about-visual{left:100px;top:170px;width:380px;height:250px;background:radial-gradient(circle at 45% 55%,#3a3a3a 0%,#1a1a1a 55%,var(--dark) 75%)}
.about-text{left:540px;top:48px;width:620px;font-size:14.5px;line-height:1.65;color:var(--muted)}
.about-text p+p{margin-top:8px}
.btn-red{background:var(--red);color:var(--white);font-size:12px;font-weight:700;padding:9px 16px;text-transform:uppercase;display:inline-block}

/* benefits */
.benefits{position:absolute;top:1180px;left:0;width:1200px;height:440px;background:linear-gradient(180deg,var(--red) 0%,var(--red-deep) 100%)}
.benefits-title{width:100%;top:78px;text-align:center;font-size:40px}
.feature{top:160px;width:240px;text-align:center}
.feature svg{display:block;margin:0 auto 12px}
.feature p{font-size:20px;line-height:1.2}

/* services */
.services{position:absolute;top:1620px;left:0;width:1200px;height:620px;background:var(--dark)}
.services-title{left:100px;top:166px;font-size:50px}
.services-text{left:100px;top:238px;width:480px;font-size:14.5px;line-height:1.6;color:var(--muted)}
.service-list{left:100px;top:356px;list-style:none;font-size:24px;font-weight:500}
.service-list li{display:flex;align-items:center;gap:16px;margin-bottom:18px}
.service-list li::before{content:"";width:12px;height:12px;border-radius:50%;background:var(--red)}
.services-visual{left:620px;top:120px;width:540px;height:430px;border-radius:0 0 180px 0;border:6px solid var(--red);background:linear-gradient(135deg,#1b2c4a 0%,#3f6fa8 45%,#0d0d12 100%)}

/* footer */
.footer{position:absolute;top:2240px;left:0;width:1200px;height:480px;background:var(--black)}
.footer-card{left:100px;top:110px;width:360px;height:260px;background:var(--red);padding:26px 24px}
.footer-card .brand{color:var(--white);font-size:72px;line-height:1}
.footer-card p{font-size:14px;line-height:1.5;margin:18px 0 16px}
.footer-card .signup-form{width:100%;height:36px;background:transparent;border:2px solid var(--white)}
.footer-card .signup-form span{color:var(--white);padding:8px 12px}
.footer-card .signup-form b{background:var(--white);color:var(--red);padding:9px 22px}
.col{top:100px}
.col h4{font-size:22px;font-weight:600;margin-bottom:10px}
.col a{display:block;font-size:14px;line-height:1.6;color:var(--muted);text-decoration:none}
.socials{display:flex;gap:14px;margin-top:12px}
.socials i{width:24px;height:24px;border-radius:50%;background:var(--red)}
.footer-rule{left:0;top:390px;width:1200px;height:1px;background:#333}
.copyright{width:100%;top:414px;text-align:center;font-size:14px;color:var(--muted)}
.pay{right:100px;top:412px;display:flex;gap:10px}
.pay i{width:36px;height:22px;border-radius:3px;background:#d9d9d9}
</style>
</head>
<body>

<section class="hero">
  <svg class="hero-band" width="760" height="720" viewBox="0 0 760 720" aria-hidden="true">
    <polygon points="170,0 760,0 760,720 620,720 520,240 90,120" fill="#e3141b"/>
    <polygon points="330,0 760,0 760,520 620,180" fill="#b10e13" opacity=".55"/>
  </svg>
  <nav class="nav">
    <div class="brand">VIRELO</div>
    <div class="nav-links"><span>Home</span><span>Product</span><span>Account Information</span></div>
    <div class="btn-outline">Sign Up</div>
  </nav>
  <h1 class="abs display hero-title">UNLIMITED MOVIES, TV SHOWS AND MORE</h1>
  <p class="abs hero-text">Lorem ipsum dolor sit amet, consectetur adipiscing elit, sed do eiusmod tempor incididunt ut labore et dolore magna.</p>
  <div class="abs signup-form" style="left:100px;top:388px"><span>Enter Email</span><b>Submit</b></div>
  <div class="abs hero-visual" role="img" aria-label="Action movie scene shown on a TV, laptop, tablet and phone"></div>
</section>

<section class="about">
  <h2 class="abs display about-title">WHAT CAN VIRELO DO FOR YOU?</h2>
  <div class="abs about-visual" role="img" aria-label="IPTV streaming box with remote control"></div>
  <div class="abs about-text">
    <p>Lorem ipsum dolor sit amet, consectetur adipiscing elit, sed do eiusmod tempor incididunt ut labore et dolore magna aliqua. Ut enim ad minim veniam, quis nostrud exercitation ullamco laboris nisi ut aliquip ex ea commodo consequat. Duis aute irure dolor in reprehenderit in voluptate velit esse cillum dolore eu fugiat nulla pariatur. Excepteur sint occaecat cupidatat non proident, sunt in culpa qui officia deserunt mollit anim id est laborum.</p>
    <p>Lorem ipsum dolor sit amet, consectetur adipiscing elit, sed do eiusmod tempor incididunt ut labore et dolore magna aliqua. Ut enim ad minim veniam, quis nostrud exercitation ullamco laboris nisi ut aliquip ex ea commodo consequat.</p>
    <p style="margin-top:18px"><span class="btn-red">Contact Us</span></p>
  </div>
</section>

<section class="benefits">
  <h2 class="abs display benefits-title">BENEFITS AND FEATURES</h2>
  <div class="abs feature" style="left:40px">
    <svg width="124" height="124" viewBox="0 0 124 124" aria-hidden="true"><circle cx="62" cy="62" r="58" fill="none" stroke="#fff" stroke-width="3"/><rect x="34" y="38" width="56" height="38" rx="3" fill="none" stroke="#fff" stroke-width="3"/><path d="M50 86h24M62 76v10" stroke="#fff" stroke-width="3"/></svg>
    <p>Rock Solid TV<br>Platform</p>
  </div>
  <div class="abs feature" style="left:332px">
    <svg width="124" height="124" viewBox="0 0 124 124" aria-hidden="true"><circle cx="62" cy="62" r="58" fill="none" stroke="#fff" stroke-width="3"/><path d="M40 66v-8a22 22 0 0 1 44 0v8" fill="none" stroke="#fff" stroke-width="3"/><rect x="34" y="62" width="10" height="18" rx="3" fill="#fff"/><rect x="80" y="62" width="10" height="18" rx="3" fill="#fff"/><path d="M85 80q0 10-16 10" fill="none" stroke="#fff" stroke-width="3"/></svg>
    <p>Excellent<br>Support</p>
  </div>
  <div class="abs feature" style="left:620px">
    <svg width="124" height="124" viewBox="0 0 124 124" aria-hidden="true"><circle cx="62" cy="62" r="58" fill="none" stroke="#fff" stroke-width="3"/><path d="M52 40h20l-6 10q18 8 18 26a12 12 0 0 1-12 12H52a12 12 0 0 1-12-12q0-18 18-26z" fill="none" stroke="#fff" stroke-width="3"/><text x="62" y="80" text-anchor="middle" fill="#fff" font-family="Poppins,sans-serif" font-size="20" font-weight="700">$</text></svg>
    <p>Cost<br>Effective</p>
  </div>
  <div class="abs feature" style="left:908px">
    <svg width="124" height="124" viewBox="0 0 124 124" aria-hidden="true"><circle cx="62" cy="62" r="58" fill="none" stroke="#fff" stroke-width="3"/><rect x="40" y="34" width="38" height="52" rx="3" fill="none" stroke="#fff" stroke-width="3"/><path d="M48 48h22M48 58h22M48 68h12" stroke="#fff" stroke-width="3"/><circle cx="78" cy="78" r="9" fill="#e3141b" stroke="#fff" stroke-width="3"/></svg>
    <p>Licensing</p>
  </div>
</section>

<section class="services">
  <h2 class="abs display services-title">OUR SERVICE PROVIDE</h2>
  <p class="abs services-text">Lorem ipsum dolor sit amet, consectetur adipiscing elit, sed do eiusmod tempor incididunt ut labore et dolore magna aliqua. Ut enim ad minim veniam, quis nostrud exercitation ullamco laboris nisi ut aliquip ex ea commodo consequat.</p>
  <ul class="abs service-list">
    <li>Virelo IPTV service</li>
    <li>Monthly Subscription IPTV</li>
    <li>Virelo Best IPTV Channels</li>
  </ul>
  <span class="abs btn-red" style="left:100px;top:526px">Read More</span>
  <div class="abs services-visual" role="img" aria-label="Hand holding a remote in front of a TV showing a streaming series"></div>
</section>

<footer class="footer">
  <div class="abs footer-card">
    <div class="brand">VIRELO</div>
    <p>Sign Up For Our Newsletter And We'll Keep You Up-to-date With All Our IPTV Services</p>
    <div class="signup-form"><span>Enter Email</span><b>Submit</b></div>
  </div>
  <div class="abs col" style="left:600px">
    <h4>Quick Links</h4>
    <a>Home</a><a>Product</a><a>Account Information</a><a>Sign Up</a>
  </div>
  <div class="abs col" style="left:785px">
    <h4>Services</h4>
    <a>Terms of Use</a><a>Privacy</a><a>Cookie Preferences</a><a>Information</a>
  </div>
  <div class="abs col" style="left:970px">
    <h4>Help Links</h4>
    <a>Returns And Refund Policy</a><a>Payments</a>
    <h4 style="margin-top:18px">Follow Us</h4>
    <div class="socials"><i></i><i></i><i></i><i></i></div>
  </div>
  <div class="abs footer-rule"></div>
  <div class="abs copyright">2023 Virelo | All Rights Reserved.</div>
  <div class="abs pay"><i></i><i></i><i></i><i></i><i></i></div>
</footer>

</body>
</html>
```